Digital Book Cover

I am currently in the process of building a digital book for my web site but struggling with the front and back covers. We are an ecommerce business selling notice boards of all kind, indoor, outdoor, hospitality, staff boards, whiteboards, mobile and so on.

The company web site is orange and white. We already have a company logo which we would like included. The logo is simply the word "larchwick" in black and the work "company" in orange. When our web site was redesigned the company that designed it reversed the colours of the logo and had the word "larchwick" in black & "company" in white onto an orange banner. Either way I don't mind.

Target Market(s)

We sell to everyone online including schools colleges, universities, KTB, companies, churches, supermarkets, hotels etc. If fact everyone!

Industry/Entity Type

Digital

Requirements
Must have
• Company colours and include the company logo and strap line "A Notice Board For Every Location"
• Company details including postal address, phone, fax, email and web site.
• Finish cover to be supplied as a PDF

```html
<!DOCTYPE html>
<html lang="en">
<head>
<meta charset="utf-8">
<title>Larchwick Company – Digital Book Cover</title>
<link rel="stylesheet" href="https://fonts.googleapis.com/css2?family=Arimo:wght@400&display=swap">
<style>
  :root {
    --orange-deep: #e9a412;
    --orange-mid: #f2b320;
    --orange-light: #f8c23a;
    --glow: rgba(255, 255, 255, 0.22);
    --glow-soft: rgba(255, 255, 255, 0.08);
    --ink: #1a1a1a;
  }
  html, body {
    margin: 0;
    padding: 0;
    overflow: hidden;
    background: #ffffff;
  }
  .cover {
    position: relative;
    width: 848px;
    height: 1200px;
    overflow: hidden;
    background: linear-gradient(160deg, var(--orange-deep) 0%, var(--orange-mid) 55%, var(--orange-light) 100%);
    font-family: "Arimo", Arial, sans-serif;
    color: var(--ink);
  }
  .cover__backdrop {
    position: absolute;
    inset: 0;
  }
  .brand {
    position: absolute;
    left: 80px;
    top: 520px;
    margin: 0;
    font-weight: 400;
    font-size: 102px;
    line-height: 0.86;
    letter-spacing: -2px;
    color: var(--ink);
  }
  .brand__line { display: block; }
  .brand__line--second { padding-left: 210px; }
  .tagline {
    position: absolute;
    left: 56px;
    top: 716px;
    margin: 0;
    font-size: 32px;
    color: var(--ink);
  }
  .contact {
    position: absolute;
    left: 0;
    right: 0;
    top: 1088px;
    text-align: center;
    padding-left: 60px;
    margin: 0;
    font-style: normal;
  }
  .contact__web {
    display: block;
    font-size: 36px;
    color: var(--ink);
  }
  .contact__details {
    display: block;
    margin-top: 18px;
    font-size: 21px;
    color: var(--ink);
  }
</style>
</head>
<body>
  <main class="cover">
    <svg class="cover__backdrop" width="848" height="1200" viewBox="0 0 848 1200" aria-hidden="true">
      <defs>
        <radialGradient id="disc-glow" cx="0.55" cy="0.35" r="0.7">
          <stop offset="0" stop-color="#ffffff" stop-opacity="0.28"/>
          <stop offset="1" stop-color="#ffffff" stop-opacity="0.06"/>
        </radialGradient>
      </defs>
      <circle cx="485" cy="580" r="470" fill="url(#disc-glow)"/>
    </svg>

    <h1 class="brand">
      <span class="brand__line">Larchwick</span>
      <span class="brand__line brand__line--second">Company</span>
    </h1>

    <p class="tagline">A Notice Board For Every Location</p>

    <address class="contact">
      <span class="contact__web">www.larchwickcompany.com</span>
      <span class="contact__details">sales@larchwickcompany.com - 024 7655 0142</span>
    </address>
  </main>
</body>
</html>
```